Mobile Repair Service on location needs a Web Design

We are starting a new mobile device repair service called Handset Haven and our website needs a design!

Hello Designers!
First, we'd like to make clear this is more than a simple web design contest, we want the designers to create an idea. We want someone who can create the whole theme of the service's we provide. We want someone that can help design our visual branding, help us communicate a sentiment. And we are willing to pay for that.

Who are we?
Our company is based in Rotterdam, the Netherlands. We provide different services for all kinds of electronic devices. The kind of services we provide are, among other things, installations of hardware and software and the repair of broken or malfunctioning devices.
We are starting a new service that offers mobile device repairs on location, be it at the home of our customers, their office, or any other place. Just give us the address and we will come to you for the repair job. This is also our main USP. We have multiple skilled engineers who drive trough the country on a daily basis and can be on location within a working day. Repair is done immediately onsite while the customer waits. At this stage we will start with the smartphone product-group within the mobile devices. In a second phase we might also add tablets.
People don't want to be without their phone for weeks because of some parts that needed to be ordered by a repair center they had to sent their phone to. We offer a fully functional mobile repair center in the form of specially customized vans. These vans have all the tools and utilities needed by our engineers to safely repair your mobile device. Your phone is being repaired directly in front of you, the next business-day, on a location you desire.

For this new service we are creating a website called Handset Haven. The website needs a story and matching design and this is where you come in. We are not looking for a simple template design we can get from any place. We need a story. We want you to create an idea, build a unique theme or vision that helps sell the product/service. This goes beyond the design of the website. We need the whole package, the design you are creating needs to have returning elements like icons, color use, images, maybe even characters etc. You name it! There needs to be a common thread in the design so we can reuse elements in, for example, the email templates, the work order or receipt we give to our customers (we may contact the winner of the contest to design these for us as well!).

The name 'Handset Haven' is chosen. Rehab (short for rehabilitate) has a bold and playful tone to it and the design needs to reflect the name. So we're looking for a somewhat playful and cheeky design. Definitely not too serious and definitely modern. We already got a logo that we love and that fit's this description (see attached design documents for the logo). It's bold, powerful and fun. Our web design needs to reflect this as well and has to fit in with our logo.
We would really like it if the design somehow incorporates elements that highlight our unique selling points (repairs on location, we come to you etc.). We would really like some form of story telling in the design. Think clumsy people breaking their phones. Teenagers in tears because they have no access to their friends. People nowadays have the need to always be 'connected'. What happens when your phone is broken or malfunctioning? We're handling tech, we are nerds and a little bit weird, but we're professionals and here to help you with your problem. The sentiment Byte Brigade tries to communicate is something we really like. We're looking for fresh idea's, anything goes!

In an overview all Unique Selling Points of the Handset haven service:
- Professional service on location. Don’t ship to us we will come to you!
- Clear pricing upfront. No hidden cost.
- Next business-day repair.
- Backed by a professional call center open 12 hours a day and open on a Saturday as well
- Backed by a professional repair center with more then 12 years of experience
- Repair is done by certified engineers
- 1 year warranty on the repair

The process:
The main function of our website will be for customers to make a repair request. A customer will visit our website and can make a repair request immediately by going through a 'request-order-flow'. In this flow he or she will need to fill in some forms and can select wich type/model/brand of mobile device he or she has and what parts need to be repaired. After a request is placed we will call the customer back (within an hour) for a short intake and to set a date/time and location. Our engineer will meet the customer at the specified location and will repair the device onsite in one of our mobile repair centers, which is a specialized van equipped with all the tools needed for device restorations.
So in short the steps are:
- Choose your device and repair job
- Place the order
- Get a callback within the hour
- Set date and location
- We will come to you.

Website functionality:
Our website is our main form of communication. So the sentiment we want to communicate needs be reflected in the design. We need a main/front page designed (preferably a long scrolling page design) containing:
1. Customers will be able to request a repair job directly on our website. So there will need to be a prominent button/link at the top of our main page that will bring the customer to this 'request-order-flow'. This is the main flow which needs to be full focus on the front page. All other items are secondary.
2. The general information of who we are and what we do, and why the customer should choose us. Preferably in short bullet-point type keywords/sentences with icons or other visual cues. See our unique selling points to get an idea of the information that will be displayed here.
3. There needs to be a section that will explain the process (see above) of a repair request step-by- step, again in brief short key sentences and with (custom) icons.
4. There needs to be a section that explains to the customer he/she can always contact us if they are not sure what the problem is with their device, and for this reason are not sure what repair request they should order.
5. We want to implement some functionality that display customer ratings or customer reviews. So there needs to be room for some kind of widget of plugin we're going to implement which shows these reviews.
6. A 'For business section' where we will explain all the options we provide for corporate clients.
7. Social media links.
8. There needs to be a menu with buttons that leads to the all sections described in the previous points.

For now, we need a design for our front page. In the second phase, when we have picked our winner, we may ask the winner to design the page(s) for our request workflow as well.

EDIT:
Finally, we have a very specific order in mind for the different segments of our website. We would like you to add some more segments that were not in our original brief as well:

1. Top header with order/request button. (should instantly make clear our main USP, we do repairs on location)
2. Our process
3. Our unique selling points / why choose us
4. The kind of repairs we do (broken screens, broken batteries, water damage, broken camera's, no sound etc.)
5. A 'meet our team' section, where we introduce some of our engineers
6. A 'contact us for any questions' section/
7. Testimonials/user reviews
8. A section where we show key performance indicators
9. 'For businesses' sections
10.'Subscribe for newsletter' field
11. Social media buttons

Industry/Entity Type

It Service

Number of Pages Required

1 page

Font styles to use
Sans Serif

Requirements
Must have
• a main/front page, design only
• custom icons/images for banners, adverts online and in print (high res)
Nice to have
• Storytelling in our design.
• Design that fits with our brand new logo.
• Elements like icons to have a flat design.
• Keep in mind that the website will need to be responsive when designing! (Ideally provide an example of the mobile design as well)
• Create a fun and trustworthy feeling.

```html
<!DOCTYPE html>
<html lang="en">
<head>
<meta charset="utf-8">
<title>Handset Haven – Mobile Repair On Location</title>
<link href="https://fonts.googleapis.com/css2?family=Oswald:wght@400;500;700&family=Roboto:wght@400;500;700&display=swap" rel="stylesheet">
<style>
:root{
  --orange:#f26522;
  --orange-dark:#d9531a;
  --ink:#2b2b2b;
  --text:#555;
  --muted:#888;
  --footer:#3b3b3d;
  --footer-deep:#2e2e30;
  --lavender:#bcb8de;
  --cream:#fdf7d8;
  --white:#fff;
  --line:#dcdcdc;
}
*{box-sizing:border-box;margin:0;padding:0}
html,body{width:1200px;height:3822px;overflow:hidden}
body{font-family:'Roboto',sans-serif;color:var(--text);background:var(--white);position:relative}
.section{position:absolute;left:0;width:1200px;overflow:hidden}
.abs{position:absolute}
.heading{font-family:'Oswald',sans-serif;font-weight:500;color:var(--ink);text-transform:uppercase;font-size:24px;letter-spacing:.3px}
.heading.center{text-align:center;width:100%}
.body-copy{font-size:12.5px;line-height:1.6;color:var(--text)}
.btn{background:var(--orange);color:var(--white);font-family:'Oswald',sans-serif;text-transform:uppercase;font-size:15px;display:flex;align-items:center;justify-content:center;letter-spacing:.3px}
.placeholder{position:absolute}

/* header & hero */
.hero{top:0;height:612px}
.hero-photo{inset:0;background:linear-gradient(180deg,#2d3a4a 0%,#4b5866 38%,#55603f 70%,#3d4a2c 100%)}
.topbar{position:absolute;top:0;left:0;width:100%;height:110px;background:linear-gradient(180deg,rgba(0,0,0,.45),rgba(0,0,0,0))}
.brand{position:absolute;left:168px;top:14px;display:flex;align-items:center;gap:12px}
.brand-dot{width:62px;height:62px;border-radius:50%;background:var(--white)}
.brand-name{font-family:'Oswald',sans-serif;font-weight:700;font-size:28px;line-height:.95;color:var(--white);text-transform:uppercase}
.brand-tag{font-size:10px;color:var(--white);display:block;font-family:'Roboto',sans-serif;font-weight:400;text-transform:none;margin-top:4px}
.contact-strip{position:absolute;top:14px;left:428px;font-size:13px;color:var(--white);display:flex;gap:40px;align-items:center}
.contact-strip span{display:flex;align-items:center;gap:6px}
.contact-strip b{font-weight:700}
.mini-ico{width:16px;height:16px;border-radius:50%;background:var(--orange);display:inline-block}
.socials-top{position:absolute;left:880px;top:12px;display:flex;gap:12px}
.socials-top i{width:16px;height:16px;border-radius:3px;background:rgba(255,255,255,.85);display:block}
.nav{position:absolute;top:43px;left:465px;display:flex;height:54px;align-items:center}
.nav a{color:var(--white);font-family:'Oswald',sans-serif;font-size:14px;text-decoration:none;padding:0 22px;height:54px;display:flex;align-items:center}
.nav a.active{border-bottom:3px solid var(--orange)}
.nav .btn{height:54px;padding:0 22px;margin-left:12px}
.hero-banner{position:absolute;left:320px;top:168px;width:580px;height:200px}
.hero-banner-text{position:absolute;left:330px;top:224px;width:560px;text-align:center;color:var(--white);font-family:'Oswald',sans-serif;text-transform:uppercase}
.hero-banner-text .l1{font-size:34px;letter-spacing:2px;line-height:1}
.hero-banner-text .l2{font-size:56px;font-weight:700;line-height:1.05;letter-spacing:1px}
.hero-banner-text .l3{font-family:'Roboto',sans-serif;font-size:19px;font-weight:500;text-transform:uppercase;line-height:1.2}
.hero-van{left:172px;top:492px;width:212px;height:128px;border-radius:20px 60px 10px 10px;background:linear-gradient(180deg,#f4f4f4,#cfd1d3)}
.dots{position:absolute;top:553px;left:555px;display:flex;gap:9px}
.dots i{width:12px;height:12px;border-radius:50%;background:rgba(255,255,255,.7);display:block}
.dots i.on{background:var(--orange)}

/* who we are */
.about{top:612px;height:700px}
.about-col{left:173px;width:410px}
.about-photo{left:612px;top:45px;width:488px;height:605px;background:linear-gradient(160deg,#e9edf1 0%,#b7c2cf 45%,#2f4a7a 75%,#f2f2f2 100%)}
.ticks{list-style:none;margin-top:20px}
.ticks li{font-size:12.5px;line-height:1;margin-bottom:15px;display:flex;align-items:center;gap:10px;color:var(--text)}

/* why choose */
.why{top:1366px;height:622px;background:var(--orange)}
.why-photo{left:0;top:0;width:560px;height:622px;background:linear-gradient(180deg,#6f8aa8 0%,#3b5a8c 45%,#26386a 100%);clip-path:polygon(0 0,100% 0,470px 100%,0 100%)}
.badge-circle{position:absolute;left:292px;top:300px;width:120px;height:120px;border-radius:50%;background:var(--white);border:6px solid var(--orange);display:flex;align-items:center;justify-content:center;text-align:center;font-family:'Oswald',sans-serif;font-weight:700;color:var(--orange);font-size:17px;line-height:1}
.usp{position:absolute;width:124px;text-align:center;color:var(--white);font-size:11.5px;font-weight:500;line-height:1.35}
.usp .circ{width:78px;height:78px;border-radius:50%;background:#3a3a3c;margin:0 auto 12px;display:flex;align-items:center;justify-content:center}

/* process */
.process{top:1988px;height:292px}
.step{position:absolute;top:125px;width:150px;text-align:center;font-size:12px;color:var(--ink);line-height:1.35}
.step .circ{width:98px;height:98px;border-radius:50%;border:4px solid #eee;margin:0 auto 12px;display:flex;align-items:center;justify-content:center;background:var(--white);box-shadow:0 0 0 1px #e2e2e2}
.step-arrow{position:absolute;top:172px;color:#bbb;font-size:20px}

/* repair request */
.request{top:2280px;height:320px;background:var(--cream)}
.request-illus{left:112px;top:26px;width:234px;height:244px;border-radius:8px;background:linear-gradient(180deg,#f9e7b9,#c9cfd6)}
.request-pin{left:350px;top:20px}
.request-form{position:absolute;left:382px;top:40px;width:612px;height:242px;border:3px solid var(--orange);background:var(--white)}
.request-form .heading{position:absolute;top:14px;width:100%;text-align:center;font-size:22px}
.field{position:absolute;height:35px;border:1px solid var(--line);font-size:12px;color:var(--muted);display:flex;align-items:center;padding:0 12px;justify-content:space-between;background:var(--white)}
.radio{display:flex;align-items:center;gap:6px;font-size:12px;color:var(--text)}
.radio i{width:12px;height:12px;border-radius:50%;border:1px solid #aaa;display:block}
.radio i.on{border:4px solid var(--orange)}

/* testimonials */
.reviews{top:2600px;height:408px;background:var(--lavender)}
.review-card{position:absolute;top:124px;width:416px;height:232px;background:var(--white);padding:38px 28px 0;text-align:center}
.review-card p{font-style:italic;font-size:12.5px;line-height:1.6;color:var(--text)}
.stars{position:absolute;right:22px;top:14px;color:var(--orange);font-size:14px;letter-spacing:1px}
.quote{position:absolute;left:50%;top:6px;transform:translateX(-50%);font-family:'Oswald',sans-serif;font-size:38px;color:var(--ink);line-height:1}
.author{display:flex;align-items:center;gap:12px;justify-content:center;margin-top:18px;text-align:left}
.avatar{width:58px;height:58px;border-radius:50%;background:linear-gradient(180deg,#c9b5a2,#8d7766)}
.author b{display:block;font-size:12px;color:var(--ink);font-weight:500}
.author span{font-size:11px;color:var(--muted)}

/* corporate */
.corporate{top:3008px;height:560px}
.corp-card{position:absolute;top:126px;width:274px}
.corp-img{height:184px;width:100%}
.corp-card h3{font-size:14px;color:var(--ink);font-weight:700;margin-top:18px;line-height:1.3}
.corp-card p{font-size:11.5px;line-height:1.55;color:var(--muted);margin-top:12px}
.corp-card .btn{width:78px;height:28px;font-size:12px;margin-top:18px}

/* footer */
.footer{top:3567px;height:255px;background:var(--footer)}
.up-tab{position:absolute;left:550px;top:-1px}
.footer .col{position:absolute;top:40px;color:#d6d6d6;font-size:12px;line-height:1.55}
.footer h4{font-family:'Oswald',sans-serif;font-weight:500;color:var(--white);font-size:13px;text-transform:uppercase;margin-bottom:10px}
.footer .big{font-size:21px;color:var(--white);font-weight:500}
.newsletter{display:flex;margin-top:10px}
.newsletter .inp{width:226px;height:34px;background:var(--white);font-size:11px;color:var(--muted);display:flex;align-items:center;padding:0 10px}
.newsletter .btn{width:82px;height:34px;font-size:12px}
.socials{display:flex;gap:18px;margin-top:10px}
.socials i{width:20px;height:20px;border-radius:4px;background:#9a9a9c;display:block}
.copyright{position:absolute;left:173px;top:225px;font-size:11px;color:#aaa}
</style>
</head>
<body>

<header class="section hero">
  <div class="placeholder hero-photo" role="img" aria-label="City skyline at dusk seen over trees"></div>
  <div class="topbar"></div>
  <div class="brand">
    <span class="brand-dot"></span>
    <div class="brand-name">Handset<br>Haven<span class="brand-tag">We will come to you!</span></div>
  </div>
  <div class="contact-strip">
    <span><i class="mini-ico"></i>Call Us Today: <b>(100) 000-000</b></span>
    <span><i class="mini-ico"></i>Email Us : <b>info@handsethaven.com</b></span>
  </div>
  <div class="socials-top"><i></i><i></i><i></i><i></i></div>
  <nav class="nav">
    <a class="active">HOME</a><a>ABOUT US</a><a>SERVICES</a><a>CONTACT US</a>
    <span class="btn">Request Order Flow</span>
  </nav>
  <svg class="hero-banner" viewBox="0 0 580 200" preserveAspectRatio="none" aria-hidden="true">
    <path d="M40 26 Q150 6 290 18 Q430 4 548 22 L536 70 L574 100 L540 148 Q430 172 290 186 Q150 196 28 180 L46 126 L6 98 L42 62 Z" fill="#f26522"/>
  </svg>
  <div class="hero-banner-text">
    <div class="l1">Professional Service</div>
    <div class="l2">On Location.</div>
    <div class="l3">Don't ship to us we will come to you!</div>
  </div>
  <div class="placeholder hero-van" role="img" aria-label="White service van with company livery"></div>
  <div class="dots"><i class="on"></i><i></i><i></i><i></i><i></i></div>
</header>

<section class="section about">
  <div class="abs about-col" style="top:56px">
    <h2 class="heading">Who We Are</h2>
    <p class="body-copy" style="margin-top:18px">Lorem ipsum dolor sit amet, consectetur adipisicing elit, sed do eiusmod tempor incididunt ut labore et dolore magna aliqua. Ut enim ad minim veniam, quis nostrud exercitation ullamco laboris nisi ut aliquip ex ea commodo consequat. Duis aute irure dolor in reprehenderit in voluptate velit esse cillum dolore eu fugiat nulla pariatur. Excepteur sint occaecat cupidatat non proident, sunt in culpa qui officia deserunt mollit anim id est laborum.</p>
    <p class="body-copy" style="margin-top:14px">Lorem ipsum dolor sit amet, consectetur adipisicing elit, sed do eiusmod tempor incididunt ut labore et dolore magna aliqua. Ut enim ad minim veniam, quis nostrud exercitation ullamco laboris nisi ut aliquip ex ea commodo consequat.</p>
    <h2 class="heading" style="margin-top:48px">What We Do</h2>
    <p class="body-copy" style="margin-top:18px">Lorem ipsum dolor sit amet, consectetur adipisicing elit, sed do eiusmod tempor incididunt ut labore et dolore magna aliqua. Ut enim ad minim veniam, quis nostrud exercitation ullamco.</p>
    <ul class="ticks">
      <li><svg width="14" height="14" viewBox="0 0 14 14"><path d="M2 7l3 3 7-7" stroke="#f26522" stroke-width="2" fill="none"/></svg>Lorem ipsum dolor sit amet, consectetur adipiscing elit.</li>
      <li><svg width="14" height="14" viewBox="0 0 14 14"><path d="M2 7l3 3 7-7" stroke="#f26522" stroke-width="2" fill="none"/></svg>Fusce ornare dolor quis erat dignissim, sed imperdiet purus mattis.</li>
      <li><svg width="14" height="14" viewBox="0 0 14 14"><path d="M2 7l3 3 7-7" stroke="#f26522" stroke-width="2" fill="none"/></svg>Vivamus pulvinar neque ac scelerisque semper.</li>
      <li><svg width="14" height="14" viewBox="0 0 14 14"><path d="M2 7l3 3 7-7" stroke="#f26522" stroke-width="2" fill="none"/></svg>Mauris vulputate tortor vel sapien ornare fringilla.</li>
      <li><svg width="14" height="14" viewBox="0 0 14 14"><path d="M2 7l3 3 7-7" stroke="#f26522" stroke-width="2" fill="none"/></svg>Fusce imperdiet nunc at tempor pretium.</li>
    </ul>
  </div>
  <div class="placeholder about-photo" role="img" aria-label="Engineer in uniform holding a tablet beside a white service van"></div>
</section>

<section class="section why">
  <div class="placeholder why-photo" role="img" aria-label="Smiling engineer in cap and blue uniform holding a tablet"></div>
  <div class="badge-circle">Handset<br>Haven</div>
  <h2 class="heading abs" style="color:#fff;left:560px;width:372px;text-align:center;top:40px;font-size:22px">Why The Customer Should Choose Us</h2>
  <div class="usp" style="left:539px;top:130px"><div class="circ"><svg width="36" height="36" viewBox="0 0 36 36" fill="none" stroke="#fff" stroke-width="2"><path d="M18 30s-9-9-9-15a9 9 0 0 1 18 0c0 6-9 15-9 15z"/><circle cx="18" cy="15" r="3"/></svg></div>Professional service on location. Don't ship to us we will come to you!</div>
  <div class="usp" style="left:685px;top:130px"><div class="circ"><svg width="36" height="36" viewBox="0 0 36 36" fill="none" stroke="#fff" stroke-width="2"><rect x="7" y="11" width="22" height="16" rx="2"/><path d="M7 15h22"/></svg></div>Clear pricing upfront.<br>No hidden cost.</div>
  <div class="usp" style="left:830px;top:130px"><div class="circ"><svg width="36" height="36" viewBox="0 0 36 36" fill="none" stroke="#fff" stroke-width="2"><path d="M5 12h17v12H5zM22 16h6l3 4v4h-9z"/><circle cx="11" cy="26" r="2"/><circle cx="26" cy="26" r="2"/></svg></div>Next business-day<br>repair.</div>
  <div class="usp" style="left:460px;top:335px"><div class="circ"><svg width="36" height="36" viewBox="0 0 36 36" fill="none" stroke="#fff" stroke-width="2"><rect x="10" y="7" width="16" height="22" rx="2"/><path d="M14 13h8M14 18h8"/></svg></div>Repair is done by certified engineers</div>
  <div class="usp" style="left:611px;top:335px"><div class="circ"><svg width="36" height="36" viewBox="0 0 36 36" fill="none" stroke="#fff" stroke-width="2"><rect x="7" y="10" width="22" height="16"/><path d="M12 18h12"/></svg></div>1 year warranty on<br>the repair</div>
  <div class="usp" style="left:756px;top:335px"><div class="circ"><svg width="36" height="36" viewBox="0 0 36 36" fill="none" stroke="#fff" stroke-width="2"><path d="M11 7h14M11 29h14M13 7c0 8 10 8 10 22M23 7c0 8-10 8-10 22"/></svg></div>Backed by a professional repair center with more then 12 years of experience</div>
  <div class="usp" style="left:901px;top:335px"><div class="circ"><svg width="36" height="36" viewBox="0 0 36 36" fill="none" stroke="#fff" stroke-width="2"><circle cx="18" cy="15" r="6"/><path d="M8 30c2-6 18-6 20 0M10 15a8 8 0 0 1 16 0"/></svg></div>Backed by a professional call center open 12 hours a day and open on a Saturday as well</div>
</section>

<section class="section process">
  <h2 class="heading center abs" style="top:50px;font-size:22px">The Process</h2>
  <div class="step" style="left:187px"><div class="circ"><svg width="40" height="40" viewBox="0 0 40 40" fill="none" stroke="#f26522" stroke-width="2"><rect x="12" y="5" width="16" height="30" rx="3"/><path d="M18 30h4"/></svg></div>Choose your device<br>and repair job</div>
  <div class="step-arrow" style="left:335px">→</div>
  <div class="step" style="left:358px"><div class="circ"><svg width="40" height="40" viewBox="0 0 40 40" fill="none" stroke="#f26522" stroke-width="2"><path d="M6 8h5l4 17h16l3-12H13"/><circle cx="17" cy="31" r="2"/><circle cx="28" cy="31" r="2"/></svg></div>Place the order</div>
  <div class="step-arrow" style="left:508px">→</div>
  <div class="step" style="left:531px"><div class="circ"><svg width="40" height="40" viewBox="0 0 40 40" fill="none" stroke="#f26522" stroke-width="2"><circle cx="20" cy="20" r="14"/><path d="M14 14c0 8 4 12 12 12l2-3-4-2-2 2c-2-1-4-3-5-5l2-2-2-4z"/></svg></div>Get a callback<br>within the hour</div>
  <div class="step-arrow" style="left:679px">→</div>
  <div class="step" style="left:702px"><div class="circ"><svg width="40" height="40" viewBox="0 0 40 40" fill="none" stroke="#f26522" stroke-width="2"><rect x="7" y="9" width="26" height="24" rx="2"/><path d="M7 16h26M13 6v6M27 6v6"/></svg></div>Set date and<br>location</div>
  <div class="step-arrow" style="left:845px">→</div>
  <div class="step" style="left:868px"><div class="circ"><svg width="40" height="40" viewBox="0 0 40 40" fill="none" stroke="#f26522" stroke-width="2"><path d="M5 14h20v12H5zM25 18h6l4 4v4H25z"/><circle cx="11" cy="28" r="2"/><circle cx="29" cy="28" r="2"/></svg></div>We will come to you</div>
</section>

<section class="section request">
  <div class="placeholder request-illus" role="img" aria-label="Cartoon engineer with a screwdriver beside a friendly phone character"></div>
  <svg class="abs request-pin" width="60" height="76" viewBox="0 0 60 76" aria-hidden="true"><path d="M30 74S4 44 4 28a26 26 0 0 1 52 0c0 16-26 46-26 46z" fill="#f26522"/><circle cx="30" cy="28" r="18" fill="#fff"/></svg>
  <div class="request-form">
    <h2 class="heading">A Repair Request</h2>
    <div class="field" style="left:23px;top:56px;width:562px">What parts need to be repaired</div>
    <div class="field" style="left:23px;top:117px;width:192px">Model<svg width="10" height="6" viewBox="0 0 10 6"><path d="M0 0l5 6 5-6z" fill="#f26522"/></svg></div>
    <div class="field" style="left:240px;top:117px;width:192px">Brand<svg width="10" height="6" viewBox="0 0 10 6"><path d="M0 0l5 6 5-6z" fill="#f26522"/></svg></div>
    <div class="radio abs" style="left:466px;top:128px"><i class="on"></i>He</div>
    <div class="radio abs" style="left:522px;top:128px"><i></i>She</div>
    <div class="btn abs" style="left:23px;top:178px;width:562px;height:38px">Place The Order</div>
  </div>
</section>

<section class="section reviews">
  <svg class="abs" style="top:0;left:0" width="1200" height="40" viewBox="0 0 1200 40" preserveAspectRatio="none" aria-hidden="true"><path d="M0 0H1200V18Q1120 36 1020 18T820 18T620 18T420 18T220 18T0 18Z" fill="#fdf7d8"/></svg>
  <h2 class="heading center abs" style="top:58px;font-size:22px">What Our Customers Say</h2>
  <div class="review-card" style="left:173px">
    <span class="quote">“</span><span class="stars">★★★★★</span>
    <p>Lorem ipsum dolor sit amet, consectetur adipisicing elit, sed do eiusmod tempor incididunt ut labore et dolore magna aliqua. Ut enim ad minim veniam, quis nostrud exercitation ullamco laboris nisi ut aliquip ex ea commodo consequat.</p>
    <div class="author"><div class="avatar" role="img" aria-label="Customer portrait"></div><div><b>Sam Verhoef</b><span>Lorem ipsum dolor</span></div></div>
  </div>
  <div class="review-card" style="left:612px">
    <span class="stars">★★★★★</span>
    <p>Lorem ipsum dolor sit amet, consectetur adipisicing elit, sed do eiusmod tempor incididunt ut labore et dolore magna aliqua. Ut enim ad minim veniam, quis nostrud exercitation ullamco laboris nisi ut aliquip ex ea commodo consequat.</p>
    <div class="author"><div class="avatar" role="img" aria-label="Customer portrait"></div><div><b>Lina Bakker</b><span>Lorem ipsum dolor</span></div></div>
  </div>
  <svg class="abs" style="bottom:0;left:0" width="1200" height="48" viewBox="0 0 1200 48" preserveAspectRatio="none" aria-hidden="true"><path d="M0 16Q100 40 200 20T400 20T600 20T800 20T1000 20T1200 14V48H0Z" fill="#1e1e1e"/><path d="M0 26Q100 50 200 30T400 30T600 30T800 30T1000 30T1200 24V48H0Z" fill="#fff"/></svg>
</section>

<section class="section corporate">
  <h2 class="heading center abs" style="top:50px;font-size:22px">We Provide For Corporate Clients</h2>
  <div class="corp-card" style="left:173px">
    <div class="corp-img" role="img" aria-label="Hand touching a glowing network interface" style="background:linear-gradient(135deg,#1d2a3a,#4d6b8c)"></div>
    <h3>Lorem ipsum dolor sit amet, consectetur adipiscing elit,</h3>
    <p>Sed ut perspiciatis unde omnis iste natus error sit voluptatem accusantium doloremque laudantium, totam rem aperiam, eaque ipsa quae ab illo inventore veritatis.</p>
    <div class="btn">Read More</div>
  </div>
  <div class="corp-card" style="left:466px">
    <div class="corp-img" role="img" aria-label="Support agent wearing a headset" style="background:linear-gradient(135deg,#6f4a3a,#d9b49a)"></div>
    <h3>Lorem ipsum dolor sit amet, consectetur adipiscing elit,</h3>
    <p>Sed ut perspiciatis unde omnis iste natus error sit voluptatem accusantium doloremque laudantium, totam rem aperiam, eaque ipsa quae ab illo inventore veritatis.</p>
    <div class="btn">Read More</div>
  </div>
  <div class="corp-card" style="left:757px">
    <div class="corp-img" role="img" aria-label="Business hand with interlocking gears" style="background:linear-gradient(135deg,#9aa8b6,#3c4a58)"></div>
    <h3>Lorem ipsum dolor sit amet, consectetur adipiscing elit,</h3>
    <p>Sed ut perspiciatis unde omnis iste natus error sit voluptatem accusantium doloremque laudantium, totam rem aperiam, eaque ipsa quae ab illo inventore veritatis.</p>
    <div class="btn">Read More</div>
  </div>
</section>

<footer class="section footer">
  <svg class="up-tab" width="100" height="26" viewBox="0 0 100 26" aria-hidden="true"><path d="M0 0H100Q80 0 70 16Q60 26 50 26Q40 26 30 16Q20 0 0 0Z" fill="#fff"/><path d="M44 12l6-6 6 6M50 6v12" stroke="#3b3b3d" stroke-width="2" fill="none"/></svg>
  <div class="brand" style="left:173px;top:40px">
    <span class="brand-dot"></span>
    <div class="brand-name">Handset<br>Haven<span class="brand-tag">We will come to you!</span></div>
  </div>
  <div class="btn abs" style="left:173px;top:142px;width:170px;height:36px;border-radius:18px;font-size:13px">Request Order Flow</div>
  <div class="col" style="left:428px"><h4>Quick Links</h4>Home<br>About Us<br>Services<br>Contact Us</div>
  <div class="col" style="left:566px"><h4>Contact Us</h4>Handset Haven<br>Lorem ipsum dolor<br>City<br><br>Phone<br><span class="big">(100) 000-000</span><br>Email<br>info@handsethaven.com</div>
  <div class="col" style="left:757px"><h4>Newsletter Subscribe</h4>Enter your email address below and get<br>the latest!
    <div class="newsletter"><div class="inp">Enter your Email Id here...</div><div class="btn">Subscribe</div></div>
    <h4 style="margin-top:18px">Get Connect With Us</h4>
    <div class="socials"><i></i><i></i><i></i><i></i></div>
  </div>
  <div class="copyright">© 2017 Handset Haven</div>
</footer>

</body>
</html>
```